Website Design - TallyPorchHelpers.net

PLEASE CHECK WORD DOCUMENT ATTACHED FOR WEBSITE FLOW.

Target Market(s)

REAL ESTATE AGENTS ARE THE TARGET MARKET

Industry/Entity Type

Real Estate

Coding

Coded - Design and coding required

Number of Pages Required

4 page

Colors

Designer to choose colors to be used in the design.

Requirements
Must have
• WE LIKE RED LOGO ATTACHED
Nice to have
• PLEASE CHECK WORD DOCUMENT ATTACHED FOR WEBSITE FLOW.
Should not have

```html
<!DOCTYPE html>
<html lang="en">
<head>
<meta charset="utf-8">
<title>Tally Porch Helpers</title>
<link href="https://fonts.googleapis.com/css2?family=Montserrat:wght@300;400;500;600;700&display=swap" rel="stylesheet">
<style>
:root{
  --red:#e5112b;
  --navy:#25237d;
  --ink:#222;
  --muted:#555;
  --grey-band:#f1f1f1;
  --line:#e3e3e3;
  --footer:#2b2b2b;
  --white:#fff;
}
*{box-sizing:border-box;margin:0;padding:0}
html,body{width:1200px;height:2731px;overflow:hidden}
body{position:relative;background:var(--white);font-family:Arial,Helvetica,sans-serif;color:var(--ink)}
h1,h2{font-weight:400}
.abs{position:absolute}

.top-rule{left:0;top:0;width:1200px;height:4px;background:var(--navy)}
.brand{left:86px;top:30px;display:flex;align-items:center;gap:12px;font-family:'Montserrat',sans-serif;font-weight:700;font-size:25px;color:var(--navy);line-height:1}
.brand-square{width:30px;height:30px;background:var(--navy);border-radius:4px}
.call{right:84px;top:20px;display:flex;align-items:center;gap:10px;font-family:'Montserrat',sans-serif;font-weight:500;font-size:17px;color:var(--red)}
.call-dot{width:42px;height:42px;border-radius:50%;background:var(--red);display:flex;align-items:center;justify-content:center}
.nav{right:86px;top:84px;display:flex;gap:44px;font-family:'Montserrat',sans-serif;font-weight:600;font-size:13px;color:var(--ink)}
.nav .current{color:var(--red)}

.hero{left:0;top:122px;width:1200px;height:640px}
.sign-card{left:563px;top:330px;width:389px;height:271px;background:#f7f7f5;text-align:center;font-family:'Montserrat',sans-serif;box-shadow:0 2px 6px rgba(0,0,0,.15)}
.sign-brand{margin:22px auto 0;display:inline-block;background:var(--red);color:var(--white);font-weight:700;font-size:13px;padding:8px 12px}
.sign-head{margin-top:18px;color:var(--red);font-weight:600;font-size:36px;line-height:1.1}
.sign-sub{color:var(--red);font-weight:500;font-size:24px;margin-top:6px}
.sign-line{color:var(--navy);font-weight:500;font-size:18px;margin-top:16px}
.sign-small{color:var(--navy);font-weight:500;font-size:17px;margin-top:6px}

.choose{left:0;width:1200px;text-align:center;font-family:'Montserrat',sans-serif;text-transform:uppercase;font-weight:400}
.choose-title{top:796px;font-size:35px;color:var(--red)}
.choose-sub{top:843px;font-size:24px;color:var(--navy)}
.option{top:918px;height:51px;display:flex;align-items:center;justify-content:center;font-family:'Montserrat',sans-serif;font-weight:500;font-size:14px;color:var(--white);border-radius:3px;box-shadow:0 2px 3px rgba(0,0,0,.2);white-space:nowrap}
.option.red{background:var(--red)}
.option.navy{background:var(--navy)}

.pricing{left:0;top:1042px;width:1200px;height:710px;background:var(--grey-band)}
.pricing-title{left:0;top:1085px;width:1200px;text-align:center;font-family:'Montserrat',sans-serif;font-weight:400;font-size:29px;color:var(--red)}
.pricing-lead{left:0;top:1136px;width:1200px;text-align:center;font-size:13px;color:var(--muted)}
.plan{background:var(--white);border:1px solid #ddd;box-shadow:0 1px 4px rgba(0,0,0,.12);text-align:center}
.plan-name{font-family:'Montserrat',sans-serif;font-weight:600;font-size:18px;color:var(--ink);height:56px;line-height:60px}
.plan-price{background:var(--navy);color:var(--white);font-family:'Montserrat',sans-serif;font-size:40px;height:80px;line-height:80px}
.plan-price sup{font-size:22px;vertical-align:14px}
.plan.featured .plan-price{background:var(--red);height:108px;line-height:108px}
.plan.featured .plan-name{height:60px;line-height:60px}
.plan-list{list-style:none;padding:0 10px}
.plan.featured .plan-list{padding:0 22px}
.plan-list li{font-size:12px;line-height:22px;color:var(--muted);border-bottom:1px solid var(--line);padding:14px 0}
.plan-list li:first-child{padding-top:16px}
.buy{display:inline-block;margin-top:17px;width:104px;height:37px;line-height:37px;background:var(--navy);color:var(--white);font-family:'Montserrat',sans-serif;font-weight:600;font-size:13px}
.plan.featured .buy{background:var(--red)}

.services-title{left:0;width:1200px;text-align:center;font-family:'Montserrat',sans-serif;font-weight:400;font-size:29px;text-transform:uppercase}
.service{width:240px;text-align:center}
.service-disc{width:112px;height:112px;border-radius:50%;margin:0 auto;display:flex;align-items:center;justify-content:center}
.service-name{font-family:'Montserrat',sans-serif;font-weight:600;font-size:21px;margin-top:14px}
.service-text{font-size:12.5px;line-height:26px;color:var(--ink);margin-top:4px;white-space:nowrap}
.signup{left:530px;top:2233px;width:141px;height:44px;background:var(--navy);color:var(--white);font-family:'Montserrat',sans-serif;font-weight:500;font-size:18px;display:flex;align-items:center;justify-content:center}

.newsletter{left:0;top:2322px;width:1200px;height:113px;background:var(--red)}
.newsletter-label{left:124px;top:2364px;font-family:'Montserrat',sans-serif;font-weight:400;font-size:24px;color:var(--white);white-space:nowrap}
.newsletter-input{left:430px;top:2358px;width:553px;height:42px;background:var(--white);font-size:12.5px;color:var(--ink);padding:14px 16px}
.newsletter-submit{left:983px;top:2358px;width:90px;height:42px;background:var(--navy);color:var(--white);font-family:'Montserrat',sans-serif;font-weight:600;font-size:14px;display:flex;align-items:center;justify-content:center}

.footer{left:0;top:2435px;width:1200px;height:296px;background:var(--footer)}
.footer-brand{left:0;top:2484px;width:1200px;display:flex;justify-content:center;align-items:center;gap:14px;font-family:'Montserrat',sans-serif;font-weight:700;font-size:34px;color:var(--white)}
.footer-brand .brand-square{width:40px;height:40px;background:var(--white)}
.footer-rule{left:78px;top:2569px;width:1044px;height:1px;background:#444}
.social{top:2592px;width:60px;height:60px;border:1px solid #666;border-radius:50%;display:flex;align-items:center;justify-content:center}
.copyright{left:0;top:2684px;width:1200px;text-align:center;font-size:13px;color:var(--white)}
</style>
</head>
<body>
<div class="abs top-rule"></div>

<header>
  <div class="abs brand"><span class="brand-square"></span>Tally Porch Helpers</div>
  <div class="abs call">
    <span class="call-dot"><svg width="18" height="18" viewBox="0 0 24 24"><path fill="#fff" d="M6.6 10.8a15 15 0 0 0 6.6 6.6l2.2-2.2c.3-.3.7-.4 1-.2 1.1.4 2.3.6 3.6.6.6 0 1 .4 1 1V20c0 .6-.4 1-1 1A17 17 0 0 1 3 4c0-.6.4-1 1-1h3.5c.6 0 1 .4 1 1 0 1.3.2 2.5.6 3.6.1.3 0 .7-.2 1z"/></svg></span>
    CALL US : (000)-555-0148
  </div>
  <nav class="abs nav"><span class="current">HOME</span><span>HOW IT WORKS</span><span>SERVICE</span><span>PRICING</span><span>ABOUT US</span><span>FAQ</span></nav>
</header>

<svg class="abs hero" viewBox="0 0 1200 640" role="img" aria-label="Photo of a suburban house with a green front lawn and a white open house sign post">
  <defs>
    <linearGradient id="heroFill" x1="0" y1="0" x2="0" y2="1">
      <stop offset="0" stop-color="#8d8676"/>
      <stop offset="0.45" stop-color="#6e7a4e"/>
      <stop offset="1" stop-color="#5f9a2f"/>
    </linearGradient>
  </defs>
  <polygon points="0,0 1200,0 1200,501 601,623 0,498" fill="url(#heroFill)"/>
  <polygon points="0,498 601,623 1200,501 1200,507 601,636 0,504" fill="#e5112b"/>
</svg>

<div class="abs sign-card">
  <div class="sign-brand">Tally Porch Helpers</div>
  <div class="sign-head">Helping agents save</div>
  <div class="sign-sub">time &amp; money.We place signs</div>
  <div class="sign-line">&amp; boost foot traffic to your open house</div>
  <div class="sign-small">using proven marketing techniques</div>
</div>

<section>
  <h1 class="abs choose choose-title">Choose the option below</h1>
  <h2 class="abs choose choose-sub">That best describes you</h2>
  <div class="abs option red" style="left:209px;width:239px">I'M A FULL ON BROKERAGE</div>
  <div class="abs option navy" style="left:464px;width:272px">I'M&nbsp; AN IND. BROKER WITH A TEAM</div>
  <div class="abs option red" style="left:752px;width:239px">I NEED SIGN PLACEMENT ASAP</div>
</section>

<section>
  <div class="abs pricing"></div>
  <h2 class="abs pricing-title">PRICING PACKAGES</h2>
  <p class="abs pricing-lead">Sed ut perspiciatis unde omnis iste natus error sit voluptatem accusantium doloremque laudantium</p>

  <div class="abs plan" style="left:86px;top:1215px;width:197px;height:448px">
    <div class="plan-name">5 SIGNS</div><div class="plan-price"><sup>$</sup>29</div>
    <ul class="plan-list"><li>Place signs strategically in best<br>areas according to where the<br>open house is located</li><li>Pick Up the signs after the<br>open house</li><li>Store custom signs for you<br>if needed</li></ul>
    <span class="buy">BUY NOW</span>
  </div>
  <div class="abs plan" style="left:286px;top:1215px;width:196px;height:448px">
    <div class="plan-name">10 SIGNS</div><div class="plan-price"><sup>$</sup>30</div>
    <ul class="plan-list"><li>Place signs strategically in best<br>areas according to where the<br>open house is located</li><li>Pick Up the signs after the<br>open house</li><li>Store custom signs for you<br>if needed</li></ul>
    <span class="buy">BUY NOW</span>
  </div>
  <div class="abs plan featured" style="left:481px;top:1189px;width:238px;height:499px;z-index:2">
    <div class="plan-name">15 SIGNS</div><div class="plan-price"><sup>$</sup>50</div>
    <ul class="plan-list"><li>Place signs strategically in best<br>areas according to where the<br>open house is located</li><li>Pick Up the signs after the<br>open house</li><li>Store custom signs for you<br>if needed</li></ul>
    <span class="buy">BUY NOW</span>
  </div>
  <div class="abs plan" style="left:719px;top:1215px;width:196px;height:448px">
    <div class="plan-name">20 SIGNS</div><div class="plan-price"><sup>$</sup>55</div>
    <ul class="plan-list"><li>Place signs strategically in best<br>areas according to where the<br>open house is located</li><li>Pick Up the signs after the<br>open house</li><li>Store custom signs for you<br>if needed</li></ul>
    <span class="buy">BUY NOW</span>
  </div>
  <div class="abs plan" style="left:916px;top:1215px;width:197px;height:448px">
    <div class="plan-name">25 SIGNS</div><div class="plan-price"><sup>$</sup>65</div>
    <ul class="plan-list"><li>Place signs strategically in best<br>areas according to where the<br>open house is located</li><li>Pick Up the signs after the<br>open house</li><li>Store custom signs for you<br>if needed</li></ul>
    <span class="buy">BUY NOW</span>
  </div>
</section>

<section>
  <h2 class="abs services-title" style="top:1797px;color:var(--red)">Sign up for a subscription &amp;</h2>
  <h2 class="abs services-title" style="top:1843px;color:var(--navy)">Get these marketing services for free</h2>

  <div class="abs service" style="left:92px;top:1938px">
    <div class="service-disc" style="background:var(--red)"><svg width="50" height="56" viewBox="0 0 50 56" fill="none" stroke="#fff" stroke-width="2.5"><rect x="8" y="3" width="28" height="50" rx="4"/><line x1="18" y1="47" x2="26" y2="47"/><rect x="20" y="14" width="26" height="18" rx="2" fill="#e5112b"/><line x1="25" y1="20" x2="41" y2="20"/><line x1="25" y1="26" x2="37" y2="26"/></svg></div>
    <div class="service-name" style="color:var(--red)">SMS</div>
    <p class="service-text">Send sms blast to your neighbor-<br>hood informing them your home is<br>for sale &amp; if they know anyone look-<br>ing to send them over</p>
  </div>
  <div class="abs service" style="left:350px;top:1938px">
    <div class="service-disc" style="background:var(--navy)"><svg width="56" height="50" viewBox="0 0 56 50" fill="none" stroke="#fff" stroke-width="2.5"><path d="M4 20 28 4l24 16v26H4z"/><path d="M4 20l24 16 24-16"/><line x1="4" y1="46" x2="22" y2="32"/><line x1="52" y1="46" x2="34" y2="32"/><line x1="18" y1="16" x2="38" y2="16"/><line x1="18" y1="22" x2="38" y2="22"/></svg></div>
    <div class="service-name" style="color:var(--navy)">EMAIL</div>
    <p class="service-text">Send email blast to your neighbor-<br>hood informing them your home is<br>for sale &amp; if they know anyone look-<br>ing to send them over</p>
  </div>
  <div class="abs service" style="left:608px;top:1938px">
    <div class="service-disc" style="background:var(--red)"><svg width="52" height="52" viewBox="0 0 52 52" fill="none" stroke="#fff" stroke-width="4"><rect x="6" y="22" width="26" height="14" rx="7" transform="rotate(-45 19 29)"/><rect x="20" y="16" width="26" height="14" rx="7" transform="rotate(-45 33 23)"/></svg></div>
    <div class="service-name" style="color:var(--red)">FEED AD</div>
    <p class="service-text">Newsfeed ads to people in your<br>open house area</p>
  </div>
  <div class="abs service" style="left:866px;top:1938px">
    <div class="service-disc" style="background:var(--navy)"><svg width="46" height="56" viewBox="0 0 46 56" fill="none" stroke="#fff" stroke-width="2.5"><path d="M6 3h24l10 10v40H6z"/><path d="M30 3v10h10"/><line x1="12" y1="20" x2="34" y2="20"/><line x1="12" y1="27" x2="34" y2="27"/><line x1="12" y1="34" x2="26" y2="34"/><rect x="18" y="40" width="18" height="10"/></svg></div>
    <div class="service-name" style="color:var(--navy)">VB</div>
    <p class="service-text">Send VB blast to your neighborhood<br>informing them your home is for sale<br>&amp; if they know anyone looking to<br>send them over</p>
  </div>

  <div class="abs signup">SIGN UP</div>
</section>

<section>
  <div class="abs newsletter"></div>
  <div class="abs newsletter-label">NEWSLETTER SIGNUP :</div>
  <div class="abs newsletter-input">Enter Your Email id :</div>
  <div class="abs newsletter-submit">SUBMIT</div>
</section>

<footer>
  <div class="abs footer"></div>
  <div class="abs footer-brand"><span class="brand-square"></span>TALLY PORCH HELPERS</div>
  <div class="abs footer-rule"></div>
  <div class="abs social" style="left:385px" aria-label="Social link"></div>
  <div class="abs social" style="left:458px" aria-label="Social link"></div>
  <div class="abs social" style="left:529px" aria-label="Social link"></div>
  <div class="abs social" style="left:602px" aria-label="Social link"></div>
  <div class="abs social" style="left:673px" aria-label="Social link"></div>
  <div class="abs social" style="left:744px" aria-label="Email"><svg width="20" height="15" viewBox="0 0 20 15" fill="none" stroke="#fff" stroke-width="1.6"><rect x="1" y="1" width="18" height="13" rx="1.5"/><path d="M1 2l9 7 9-7"/></svg></div>
  <p class="abs copyright">© Copyrights 2018 - Tally Porch Helpers.All Rights Reserved.</p>
</footer>
</body>
</html>
```